Develop website for Cloud Security Startup

Looking for a logo that conveys the outsourced security and management of clients data, systems and development in Tellix, Bri and Pindle with an emphasis on security and compliance

Target Market(s)

Companies looking for professional services IT firm

Coding

Coded - Design and coding required

Number of Pages Required

5+ page

Font styles to use
Sans Serif

Colors
0455a3
33a6d7

Requirements
Must have
• Landing Page
- Help me get started

Move to the cloud safely
- Benefits of Cloud

What we do
- Cloud Adoption
- Managed Services
- Optimise

Resources
- News
- Resources
- Events
- Webinars
- Not for profit
- Case Studies
- Support Button
- Incident Button

Company
- About Us
- Why Vorplexa?
- Acreditations
- Quorvane Tellix Partner
- Net Promoter Score
- Careers
- Contact Us

Contact Us

```html
<!DOCTYPE html>
<html lang="en">
<head>
<meta charset="utf-8">
<title>Vorplexa — Cloud Security</title>
<link href="https://fonts.googleapis.com/css2?family=Lato:wght@400;700;900&family=Roboto:wght@400;500&display=swap" rel="stylesheet">
<style>
:root{
  --brand:#0455a3;
  --sky:#33a6d7;
  --cyan:#1aaee6;
  --navy:#1c4f93;
  --deep:#1a5a9f;
  --ink:#222733;
  --muted:#6b7280;
  --pale:#f5f6fb;
  --white:#ffffff;
}
*{margin:0;padding:0;box-sizing:border-box}
html,body{width:1200px;height:3802px;overflow:hidden}
body{position:relative;font-family:'Roboto',Arial,sans-serif;color:var(--ink);background:var(--white)}
.abs{position:absolute}
.heading{font-family:'Lato',Arial,sans-serif}

/* hero */
.hero{position:absolute;left:0;top:0;width:1200px;height:780px;background:linear-gradient(160deg,#1c5aa3 0%,#1f6db4 45%,#1e8ac6 100%);overflow:hidden}
.brand{position:absolute;display:flex;align-items:center;gap:10px;color:var(--white);font-family:'Lato',sans-serif;font-weight:700;font-size:24px;letter-spacing:1px}
.brand .dot{width:30px;height:30px;border-radius:50%;background:var(--white)}
.auth{position:absolute;top:18px;height:38px;border-radius:19px;font:700 13px 'Lato',sans-serif;color:var(--white);display:flex;align-items:center;justify-content:center}
.auth.signup{left:826px;width:116px;background:var(--cyan)}
.auth.login{left:969px;width:121px;border:1.5px solid rgba(255,255,255,.8)}
.nav{position:absolute;top:83px;right:116px;display:flex;gap:22px;font:700 12.5px 'Lato',sans-serif;color:var(--white);text-transform:uppercase}
.nav span.drop::after{content:"";display:inline-block;width:5px;height:5px;border-right:1.5px solid #fff;border-bottom:1.5px solid #fff;transform:rotate(45deg);margin-left:5px;position:relative;top:-3px}
.hero-kicker{left:111px;top:251px;font:400 22px 'Lato',sans-serif;color:var(--white)}
.hero-title{left:109px;top:292px;width:480px;font:700 33px/43px 'Lato',sans-serif;color:var(--white)}
.hero-text{left:111px;top:395px;width:460px;font:400 14px/30px 'Lato',sans-serif;color:var(--white)}
.btn-outline{left:111px;top:474px;width:258px;height:51px;border:1.5px solid rgba(255,255,255,.85);border-radius:26px;display:flex;align-items:center;justify-content:center;gap:10px;font:700 15px 'Lato',sans-serif;color:var(--white)}
.slide-dots{left:28px;top:332px;display:flex;flex-direction:column;gap:17px}
.slide-dots i{display:block;width:16px;height:16px;border-radius:50%;border:1.5px solid rgba(255,255,255,.8)}
.slide-dots i.on{background:var(--white)}

/* about */
.about{position:absolute;left:0;top:780px;width:1200px;height:620px;background:var(--white)}
.about-photo{left:111px;top:88px;width:462px;height:446px;border-radius:14px;background:linear-gradient(135deg,#0e3b4f 0%,#12566a 45%,#0b2633 100%)}
.kicker{font:700 14px 'Lato',sans-serif;color:var(--brand);text-transform:uppercase}
.about .kicker{left:627px;top:163px}
.about-title{left:626px;top:190px;font:700 35px 'Lato',sans-serif;color:var(--ink)}
.about-text{left:630px;top:256px;width:480px;font:400 13px/28px 'Roboto',sans-serif;color:#555}
.btn-solid{display:flex;align-items:center;justify-content:center;border-radius:26px;font:700 15px 'Lato',sans-serif;color:var(--white);background:var(--navy)}
.about .btn-solid{left:626px;top:413px;width:171px;height:48px}

/* services */
.services{position:absolute;left:0;top:1400px;width:1200px;height:680px;background:linear-gradient(180deg,#2768b0 0%,#1f5aa0 100%)}
.services .kicker{left:0;width:1200px;top:38px;text-align:center;color:var(--white)}
.services-title{left:0;width:1200px;top:62px;text-align:center;font:700 42px 'Lato',sans-serif;color:var(--white)}
.svc-card{position:absolute;top:151px;width:300px;height:409px;background:var(--white);border-radius:3px;overflow:visible}
.svc-card .media{width:300px;height:222px;background:linear-gradient(135deg,#9aa3ad,#4b5563)}
.svc-card .badge{position:absolute;right:25px;top:197px;width:50px;height:50px;border-radius:50%;background:var(--white);border:2px solid #cfd7e3;display:flex;align-items:center;justify-content:center}
.svc-card h3{position:absolute;left:15px;top:240px;font:700 17px 'Lato',sans-serif;color:var(--navy)}
.svc-card p{position:absolute;left:15px;top:275px;width:275px;font:400 12.5px/24px 'Roboto',sans-serif;color:#333}
.svc-card .btn-solid{position:absolute;left:10px;top:360px;width:120px;height:35px;font-size:13px;background:var(--cyan);border-radius:18px}

/* benefits */
.benefits{position:absolute;left:0;top:2080px;width:1200px;height:677px}
.benefits .kicker{left:0;width:1200px;top:77px;text-align:center;font-weight:400;font-size:15px}
.benefits-title{left:0;width:1200px;top:103px;text-align:center;font:700 42px 'Lato',sans-serif;color:var(--ink)}
.ben-card{position:absolute;top:178px;width:318px;height:411px;background:var(--white);box-shadow:0 2px 8px rgba(0,0,0,.15)}
.ben-card .media{width:318px;height:255px}
.ben-card .icon{position:absolute;left:65px;top:210px;width:50px;height:46px;background:var(--cyan);display:flex;align-items:center;justify-content:center}
.ben-card h3{position:absolute;left:141px;top:222px;font:700 15px 'Lato',sans-serif;color:var(--ink)}
.ben-card p{position:absolute;left:9px;top:287px;width:300px;font:400 12.5px/24px 'Roboto',sans-serif;color:var(--muted)}
.ben-card a{position:absolute;left:10px;top:372px;font:500 12.5px 'Roboto',sans-serif;color:var(--navy);text-decoration:none}

/* news */
.news{position:absolute;left:0;top:2757px;width:1200px;height:640px;background:var(--pale)}
.news-panel{left:714px;top:0;width:486px;height:640px;background:var(--cyan)}
.news .kicker{left:111px;top:125px;font-weight:400;font-size:15px}
.news-title{left:110px;top:155px;font:700 50px 'Lato',sans-serif;color:var(--ink)}
.avatar{left:112px;top:224px;width:68px;height:68px;border-radius:50%;background:linear-gradient(135deg,#8b99a6,#3d4a57)}
.posted{left:190px;top:249px;font:400 15px 'Lato',sans-serif;color:#333}
.news-text{left:112px;top:305px;width:430px;font:400 13px/28px 'Roboto',sans-serif;color:#555}
.news-more{left:113px;top:432px;font:500 15px 'Roboto',sans-serif;color:var(--navy);text-decoration:underline}
.news-frame{left:565px;top:74px;width:437px;height:424px;background:var(--white);padding:10px;box-shadow:0 2px 10px rgba(0,0,0,.15)}
.news-frame div{width:100%;height:100%;background:linear-gradient(180deg,#3a4756,#1c2631 60%,#14324f)}
.arrows{left:728px;top:515px;display:flex;gap:26px}

/* footer */
.footer{position:absolute;left:0;top:3340px;width:1200px;height:462px;background:linear-gradient(180deg,#1f64ad,#1c5aa2)}
.footer .brand{left:114px;top:140px;font-size:22px}
.social{left:124px;top:234px;display:flex;gap:8px}
.social i{display:block;width:48px;height:48px;border-radius:50%;border:1.5px solid rgba(255,255,255,.8)}
.fcol{position:absolute;top:127px;color:var(--white);font:400 14px 'Roboto',sans-serif}
.fcol h4{font:700 14px 'Lato',sans-serif;text-transform:uppercase;margin-bottom:12px}
.fcol h4::after{content:"";display:block;width:30px;height:2px;background:rgba(255,255,255,.7);margin-top:12px}
.fcol li{list-style:none;line-height:30px}
.fcol .label{text-transform:uppercase;margin-top:8px}
.fcol .label:first-of-type{margin-top:0}
.fcol .val{line-height:23px}
.subscribe{margin-top:24px;width:233px;height:40px;border-radius:20px;background:var(--cyan);display:flex;align-items:center;justify-content:space-between;padding:0 10px 0 20px;font-size:12.5px}
.subscribe i{display:flex;width:22px;height:22px;border-radius:50%;background:var(--white);align-items:center;justify-content:center}
.footer-rule{left:111px;top:390px;width:977px;height:1px;background:rgba(255,255,255,.45)}
.copyright{left:111px;top:413px;font:400 14px 'Roboto',sans-serif;color:var(--white)}
.legal{right:112px;top:415px;font:400 13px 'Roboto',sans-serif;color:var(--white);text-transform:uppercase}
</style>
</head>
<body>

<header class="hero">
  <div class="brand" style="left:114px;top:44px"><span class="dot"></span>VORPLEXA</div>
  <div class="auth signup">SIGN UP</div>
  <div class="auth login">LOGIN</div>
  <nav class="nav">
    <span>Benefits of Cloud</span>
    <span class="drop">What we do</span>
    <span class="drop">Resources</span>
    <span class="drop">Company</span>
    <span>Contact Us</span>
  </nav>

  <div class="slide-dots abs"><i></i><i class="on"></i><i></i><i></i></div>
  <div class="hero-kicker abs">VORPLEXA</div>
  <h1 class="hero-title abs">Lorem ipsum dolor consectetur adipiscing elit,</h1>
  <p class="hero-text abs">Lorem ipsum dolor sit amet, consectetur adipiscing elit, eiusmod tempor incididunt ut labore et dolore magna aliqua.</p>
  <div class="btn-outline abs">HELP ME GET STARTED
    <svg width="18" height="10" viewBox="0 0 18 10"><path d="M0 5H16M12 1L16 5L12 9" fill="none" stroke="#fff" stroke-width="2"/></svg>
  </div>

  <svg class="abs" style="left:560px;top:130px" width="560" height="590" viewBox="0 0 560 590">
    <circle cx="281" cy="294" r="240" fill="none" stroke="rgba(255,255,255,.35)" stroke-width="14"/>
    <path d="M283 22 A272 272 0 0 1 283 566" fill="none" stroke="#fff" stroke-width="2"/>
    <path d="M353 78 A230 230 0 0 1 440 340" fill="none" stroke="#fff" stroke-width="2"/>
    <path d="M210 514 A230 230 0 0 1 60 300" fill="none" stroke="#fff" stroke-width="2"/>
    <circle cx="283" cy="22" r="9" fill="#fff"/>
    <circle cx="353" cy="78" r="7" fill="#fff"/>
    <circle cx="283" cy="566" r="9" fill="#fff"/>
    <circle cx="210" cy="514" r="6" fill="#fff"/>
  </svg>
  <div class="abs" role="img" aria-label="Photo of a woman in glasses working on a laptop" style="left:621px;top:204px;width:440px;height:440px;border-radius:50%;background:radial-gradient(circle at 40% 40%,#e9ebec,#c8cdd1 60%,#a9b0b6)"></div>

  <svg class="abs" style="left:0;top:700px" width="1200" height="80" viewBox="0 0 1200 80"><path d="M0 80 C250 50 520 20 720 22 C900 24 1060 50 1200 80 Z" fill="#fff"/></svg>
</header>

<section class="about">
  <div class="about-photo abs" role="img" aria-label="Photo of an engineer holding a laptop in a server room"></div>
  <div class="kicker abs">About Us</div>
  <h2 class="about-title abs">Welcome to Vorplexa</h2>
  <p class="about-text abs">Lorem ipsum dolor sit amet, consectetur adipiscing elit, sed do tempor incididunt ut labore et dolore magna aliqua. Ut enim ad minim veniam, quis nostrud exercitation ullamco laboris nisi ut aliquip ex ea commodo consequat. Duis aute irure dolor in reprehenderit in voluptate velit esse cillum dolore eu fugiat nulla pariatur.</p>
  <div class="btn-solid abs">READ MORE</div>
</section>

<section class="services">
  <div class="kicker abs">Services</div>
  <h2 class="services-title abs">What We Offered</h2>

  <article class="svc-card" style="left:128px">
    <div class="media" role="img" aria-label="Photo of hands typing on a laptop with cloud graphics"></div>
    <div class="badge"><svg width="26" height="20" viewBox="0 0 26 20"><path d="M7 18H20a5 5 0 0 0 0-10 7 7 0 0 0-13 1 4.5 4.5 0 0 0 0 9Z" fill="none" stroke="#1c4f93" stroke-width="1.6"/></svg></div>
    <h3>Cloud Adoption</h3>
    <p>Lorem ipsum dolor sit amet, adipiscing elit, sed do eiusmod tempor incididunt ut labore et dolore magna aliqua.</p>
    <div class="btn-solid">READ MORE</div>
  </article>
  <article class="svc-card" style="left:450px">
    <div class="media" role="img" aria-label="Photo of an operator in front of monitoring screens" style="background:linear-gradient(135deg,#1c3f7a,#0e1d3a)"></div>
    <div class="badge"><svg width="24" height="24" viewBox="0 0 24 24"><circle cx="12" cy="12" r="4" fill="none" stroke="#1c4f93" stroke-width="1.6"/><circle cx="12" cy="12" r="9" fill="none" stroke="#1c4f93" stroke-width="1.6" stroke-dasharray="4 3"/></svg></div>
    <h3>Managed Services</h3>
    <p>Lorem ipsum dolor sit amet, adipiscing elit, sed do eiusmod tempor incididunt ut labore et dolore magna aliqua.</p>
    <div class="btn-solid">READ MORE</div>
  </article>
  <article class="svc-card" style="left:772px">
    <div class="media" role="img" aria-label="Photo of hands on a keyboard with data graphics" style="background:linear-gradient(135deg,#e3e7ea,#b8c2ca)"></div>
    <div class="badge"><svg width="24" height="24" viewBox="0 0 24 24"><circle cx="12" cy="12" r="5" fill="none" stroke="#1c4f93" stroke-width="1.6"/><path d="M12 2V6M12 18V22M2 12H6M18 12H22M5 5L8 8M16 16L19 19M19 5L16 8M8 16L5 19" stroke="#1c4f93" stroke-width="1.6"/></svg></div>
    <h3>Optimise</h3>
    <p>Lorem ipsum dolor sit amet, adipiscing elit, sed do eiusmod tempor incididunt ut labore et dolore magna aliqua.</p>
    <div class="btn-solid">READ MORE</div>
  </article>

  <svg class="abs" style="left:0;top:590px" width="1200" height="92" viewBox="0 0 1200 92">
    <path d="M0 50 C160 48 280 55 384 80 C480 104 560 22 700 18 C780 16 860 40 960 48 L1200 48 L1200 92 L0 92 Z" fill="#fff"/>
    <path d="M0 42 C160 40 280 48 384 72 C480 96 560 14 700 10 C780 8 860 32 960 40 L1200 40" fill="none" stroke="#1aaee6" stroke-width="3"/>
  </svg>
</section>

<section class="benefits">
  <div class="kicker abs">Vorplexa</div>
  <h2 class="benefits-title abs">Benefits of Cloud</h2>

  <article class="ben-card" style="left:111px">
    <div class="media" role="img" aria-label="Photo of hands holding a cloud with a security shield" style="background:linear-gradient(180deg,#cfd8e2,#6f8aa6)"></div>
    <div class="icon"><svg width="22" height="22" viewBox="0 0 22 22"><path d="M4 11L9 16L18 6" fill="none" stroke="#fff" stroke-width="2.6"/></svg></div>
    <h3>Lorem ipsum dolor sit</h3>
    <p>Lorem ipsum dolor sit amet, adipiscing elit, sed do eiusmod tempor incididunt ut dolore magna aliqua. Ut enim ad minim veniam,</p>
    <a>READ MORE »</a>
  </article>
  <article class="ben-card" style="left:441px">
    <div class="media" role="img" aria-label="Photo of engineers at a control desk with many monitors" style="background:linear-gradient(180deg,#2f5c8c,#17263a)"></div>
    <div class="icon"><svg width="22" height="22" viewBox="0 0 22 22"><path d="M4 11L9 16L18 6" fill="none" stroke="#fff" stroke-width="2.6"/></svg></div>
    <h3>Lorem ipsum dolor sit</h3>
    <p>Lorem ipsum dolor sit amet, adipiscing elit, sed do eiusmod tempor incididunt ut dolore magna aliqua. Ut enim ad minim veniam,</p>
    <a>READ MORE »</a>
  </article>
  <article class="ben-card" style="left:770px">
    <div class="media" role="img" aria-label="Photo of a technician inspecting a server rack" style="background:linear-gradient(135deg,#3c2a6e,#151823 60%,#0f2a3a)"></div>
    <div class="icon"><svg width="22" height="22" viewBox="0 0 22 22"><path d="M4 11L9 16L18 6" fill="none" stroke="#fff" stroke-width="2.6"/></svg></div>
    <h3>Lorem ipsum dolor sit</h3>
    <p>Lorem ipsum dolor sit amet, adipiscing elit, sed do eiusmod tempor incididunt ut dolore magna aliqua. Ut enim ad minim veniam,</p>
    <a>READ MORE »</a>
  </article>
</section>

<section class="news">
  <div class="news-panel abs"></div>
  <div class="kicker abs">Vorplexa</div>
  <h2 class="news-title abs">Latest News</h2>
  <div class="avatar abs" role="img" aria-label="Author portrait"></div>
  <div class="posted abs">Posted &nbsp;By - Mira Kolden , 15-05-2021</div>
  <p class="news-text abs">Lorem ipsum dolor sit amet, consectetur adipiscing elit, sed do eiusmod tempor incididunt ut labore et dolore magna aliqua. Ut enim ad minim veniam, quis nostrud exercitation ullamco laboris nisi ut aliquip ex ea commodo consequa</p>
  <div class="news-more abs">READ MORE</div>
  <div class="news-frame abs"><div role="img" aria-label="Photo of two engineers talking in a data center aisle"></div></div>
  <div class="arrows abs">
    <svg width="32" height="14" viewBox="0 0 32 14"><path d="M31 7H3M8 2L2 7L8 12" fill="none" stroke="#fff" stroke-width="3"/></svg>
    <svg width="32" height="14" viewBox="0 0 32 14"><path d="M1 7H29M24 2L30 7L24 12" fill="none" stroke="#1c4f93" stroke-width="3"/></svg>
  </div>
</section>

<footer class="footer">
  <svg class="abs" style="left:0;top:-60px" width="1200" height="130" viewBox="0 0 1200 130">
    <path d="M0 100 C150 98 300 102 420 110 C520 118 560 40 640 40 C720 40 760 108 900 100 C1000 94 1100 96 1200 96 L1200 0 L714 0 L714 0 L0 0 Z" fill="transparent"/>
    <path d="M0 98 C150 96 300 100 420 106 C520 114 560 36 640 36 C720 36 760 104 900 98 C1000 92 1100 94 1200 94 L1200 130 L0 130 Z" fill="#1f64ad"/>
    <path d="M0 86 C150 84 300 88 420 94 C520 102 560 24 640 24 C720 24 760 92 900 86 C1000 80 1100 82 1200 82" fill="none" stroke="#1f64ad" stroke-width="3"/>
  </svg>
  <div class="brand"><span class="dot"></span>VORPLEXA</div>
  <div class="social abs" aria-label="Social links"><i></i><i></i></div>

  <div class="fcol" style="left:307px">
    <h4>Quick Links</h4>
    <ul><li>Benefits of Cloud</li><li>What we do</li><li>Resources</li><li>Company</li><li>Contact Us</li></ul>
  </div>
  <div class="fcol" style="left:465px">
    <h4>What we do</h4>
    <ul><li>Cloud Adoption</li><li>Managed Services</li><li>Optimise</li></ul>
  </div>
  <div class="fcol" style="left:654px;width:200px">
    <h4>Contact Us</h4>
    <div class="label" style="margin-top:14px">Address</div>
    <div class="val">Lorem ipsum dolor sit amet, consectetur adipiscing</div>
    <div class="label" style="margin-top:14px">Phone</div>
    <div class="val">+ 123-456-7890</div>
    <div class="label" style="margin-top:14px">Email</div>
    <div class="val">info@vorplexa.com</div>
  </div>
  <div class="fcol" style="left:871px;width:270px">
    <h4>Newsletter</h4>
    <div class="val" style="margin-top:14px">Lorem ipsum dolor sit amet, consectetur adipiscing elit, sed do eiusmod tempor</div>
    <div class="subscribe">Enter Email<i><svg width="12" height="12" viewBox="0 0 12 12"><path d="M1 6L11 1L8 11L6 7Z" fill="#1aaee6"/></svg></i></div>
  </div>

  <div class="footer-rule abs"></div>
  <div class="copyright abs">© 2021 All Rights Reserved</div>
  <div class="legal abs">Privacy Policy &nbsp;/ &nbsp;Terms &amp; Condition</div>
</footer>

</body>
</html>
```